Website & Logo The full package New Business new design and idea

Word Press

Simple, clean and very professional and approachable if possible

I am looking for a full business concept from logo to colour pallet and everything in between.
Brand new business concept, the successful applicant may continue on as our outsourced point person for all future work.

I will have an animated explainer video going over the four keys to business success Staff, Product & Services, Marketing, Sales and why the need a coach just like a sporting team to stay focused and clear on measurable outcomes.

Just added script (pdf attachment) i will be using for the explainer video at top of site.
Updates

Target Market(s)

Small business owners in Australia

Industry/Entity Type

Business Consultant

Number of Pages Required

1 page

Font styles to use
Sans Serif

Colors

Designer to choose colors to be used in the design.

Requirements
Must have
• Word press using Divi platform
• Ball park as per pdf uploaded
• Must work on all devices
• Social links
• Clear and straight forward movement through site
• Great capture of name and email,
• Free Download
• 10 Things you can start today in your small business to get you going again!
Nice to have
• clean one page potentially
• Free files and resources page
Should not have
• boring old menu and old framing

```html
<!DOCTYPE html>
<html lang="en">
<head>
<meta charset="utf-8">
<title>Bright Path Business Coach</title>
<link rel="stylesheet" href="https://fonts.googleapis.com/css2?family=Roboto:wght@300;400;500;700;900&family=Roboto+Condensed:wght@400;700&display=swap">
<style>
:root{
  --blue:#0a5bb0;
  --blue-dark:#06407f;
  --orange:#f05a28;
  --ink:#222;
  --text:#555;
  --muted:#888;
  --light:#eeeeee;
  --white:#fff;
  --footer:#141414;
  --footer-bottom:#060606;
  --yellow:#f4e7a1;
}
*{box-sizing:border-box;margin:0;padding:0}
html,body{width:1200px;height:4844px;overflow:hidden}
body{font-family:"Roboto",Arial,sans-serif;color:var(--text);background:var(--white);position:relative}
section,header,footer{position:absolute;left:0;width:1200px}
ul{list-style:none}

/* hero */
.hero{top:0;height:600px;background:linear-gradient(135deg,#3b3530 0%,#5a4d43 35%,#2e3236 60%,#4a3e34 100%)}
.hero-photo{position:absolute;inset:0}
.hero-shade{position:absolute;inset:0;background:rgba(0,0,0,.35)}
.topbar{position:absolute;top:0;left:0;width:1200px;height:80px;display:flex;align-items:center;justify-content:space-between;padding:0 24px}
.menu-toggle{width:34px;display:flex;flex-direction:column;gap:6px}
.menu-toggle span{display:block;height:4px;background:var(--white);border-radius:2px}
.brand{font-family:"Roboto Condensed",Arial,sans-serif;font-weight:700;font-size:30px;color:var(--white);letter-spacing:.3px}
.top-phone{display:flex;align-items:center;gap:10px;color:var(--white);font-size:20px}
.play{position:absolute;left:566px;top:186px;width:68px;height:68px}
.hero-title{position:absolute;top:270px;width:100%;text-align:center;color:var(--white);font-weight:900;font-size:58px;letter-spacing:.5px}
.hero-sub{position:absolute;top:360px;width:100%;text-align:center;color:var(--yellow);font-size:25px;font-weight:500}
.btn-outline-light{position:absolute;top:438px;left:500px;width:200px;height:50px;border:2px solid var(--white);border-radius:4px;color:var(--white);font-size:22px;display:flex;align-items:center;justify-content:center}

/* intro band */
.intro{top:600px;height:380px;background:linear-gradient(90deg,var(--blue-dark),var(--blue) 50%,var(--blue-dark))}
.intro-icon{position:absolute;left:542px;top:-10px;width:116px;height:116px}
.intro-text{position:absolute;top:150px;left:190px;width:820px;text-align:center;color:var(--white);font-size:15px;line-height:1.55}
.intro-text p+p{margin-top:18px}

/* snapshot */
.snapshot{top:980px;height:620px}
.framed{position:absolute}
.frame-line{position:absolute;border:2px solid var(--blue)}
.photo{position:absolute;box-shadow:0 6px 18px rgba(0,0,0,.2)}
.snapshot .frame-line{left:170px;top:110px;width:280px;height:300px}
.snapshot .photo{left:120px;top:150px;width:280px;height:300px;background:linear-gradient(140deg,#d9dde4,#9aa4b3 55%,#5c6a80)}
.snapshot-body{position:absolute;left:440px;top:138px;width:660px}
.snapshot-body h2{font-size:30px;font-weight:500;color:var(--ink)}
.date{color:var(--orange);font-size:15px;margin:6px 0 14px}
.snapshot-body p{font-size:13px;line-height:1.6}
.checklist li{position:relative;padding-left:22px;font-size:14px;line-height:1.4;margin-top:10px}
.checklist li::before{content:"";position:absolute;left:0;top:4px;width:11px;height:11px;background:var(--blue)}

/* offers */
.offers{top:1600px;height:520px;background:linear-gradient(160deg,#f4f5f8 0%,#dfe4ec 45%,#c9d1dd 70%,#eef0f4 100%)}
.slide-arrow{position:absolute;top:240px;width:26px;height:40px}
.slide-arrow.prev{left:30px}
.slide-arrow.next{right:30px}
.card{position:absolute;top:100px;width:262px;height:366px;background:var(--white);box-shadow:0 4px 16px rgba(0,0,0,.15);text-align:center;padding:100px 24px 0}
.card.c1{left:218px}
.card.c2{left:470px;top:86px;width:270px;height:380px}
.card.c3{left:790px}
.price{position:absolute;top:-46px;left:50%;margin-left:-50px;width:100px;height:100px;border-radius:50%;background:var(--blue);color:var(--white);font-size:30px;font-weight:500;display:flex;align-items:center;justify-content:center;box-shadow:0 4px 10px rgba(0,0,0,.2)}
.card.c2 .price{background:var(--orange)}
.card h3{font-size:21px;font-weight:500;color:var(--ink);line-height:1.3}
.card p{font-size:12.5px;line-height:1.5;margin-top:14px}
.btn-small{display:inline-block;margin-top:18px;padding:7px 24px;border:1px solid #999;border-radius:16px;font-size:13px;color:var(--ink)}
.card.c2 .btn-small{background:var(--orange);border-color:var(--orange);color:var(--white)}

/* how it works */
.how{top:2200px;height:520px}
.how-body{position:absolute;left:100px;top:180px;width:500px}
.how-body h2{font-size:34px;font-weight:500;color:var(--ink)}
.how-body p{font-size:13.5px;line-height:1.6;margin-top:18px}
.btn-orange{display:inline-block;margin-top:24px;padding:9px 28px;background:var(--orange);border-radius:20px;color:var(--white);font-size:15px}
.how .frame-line{left:750px;top:120px;width:330px;height:290px}
.how .photo{left:700px;top:160px;width:330px;height:290px;background:linear-gradient(150deg,#0e2d4c,#2c5f8a 50%,#8aa9c4)}

/* activities */
.activities{top:2780px;height:540px}
.wood{position:absolute;left:0;top:0;width:1200px;height:540px;background:linear-gradient(100deg,#e9e3dc 0%,#c7b39c 20%,#8b6a4d 45%,#6f5138 100%)}
.activities-panel{position:absolute;left:560px;top:0;width:640px;height:540px;background:rgba(255,255,255,.96);padding:60px 70px 0 50px}
.activities-panel h2{font-size:40px;font-weight:400;color:var(--ink);margin-bottom:22px}
.activities-panel .checklist li{font-size:14px;margin-top:9px}

/* application */
.application{top:3380px;height:400px;text-align:center}
.application h2{margin-top:55px;font-size:38px;font-weight:400;color:var(--ink)}
.application p{width:900px;margin:26px auto 0;font-size:14px;line-height:1.6}
.application a{display:inline-block;margin-top:22px;color:var(--blue);font-size:15px;font-weight:500;text-decoration:underline}

/* about */
.about{top:3820px;height:580px;background:var(--light)}
.about-body{position:absolute;left:100px;top:190px;width:490px}
.about-body h2{font-size:40px;font-weight:400;color:var(--ink)}
.about-body p{font-size:13.5px;line-height:1.6;margin-top:16px}
.about .frame-line{left:690px;top:110px;width:380px;height:390px;border-color:var(--orange)}
.about .photo{left:640px;top:60px;width:380px;height:390px;background:linear-gradient(135deg,#dfe5ec,#a7b4c2 50%,#5d6d80)}

/* footer */
.site-footer{top:4400px;height:360px;background:var(--footer);border-top:6px solid var(--blue);color:#bbb}
.footer-brand{position:absolute;left:100px;top:90px}
.footer-brand .brand{font-size:28px}
.socials{display:flex;gap:10px;margin-top:18px}
.socials span{width:30px;height:30px;border-radius:50%;border:2px solid var(--white)}
.footer-col{position:absolute;top:56px}
.footer-col h4{color:var(--white);font-size:20px;font-weight:400;letter-spacing:1px;margin-bottom:18px}
.footer-col li{font-size:14px;line-height:1.9}
.col-contact{left:460px}
.col-about{left:760px}
.col-res{left:980px}
.contact-item{display:flex;gap:12px;margin-bottom:20px}
.contact-item b{display:block;color:var(--white);font-weight:500;font-size:14px}
.contact-item span{font-size:13px}
.copyright{position:absolute;top:4760px;left:0;width:1200px;height:84px;background:var(--footer-bottom);color:#888;font-size:12px;display:flex;align-items:center;justify-content:center}
</style>
</head>
<body>

<section class="hero">
  <div class="hero-photo" role="img" aria-label="Overhead photo of a work desk with laptop, coffee and notebook"></div>
  <div class="hero-shade"></div>
  <div class="topbar">
    <div class="menu-toggle" aria-label="Menu"><span></span><span></span><span></span></div>
    <div class="brand">Bright Path Business Coach</div>
    <div class="top-phone">
      <svg width="26" height="26" viewBox="0 0 26 26"><circle cx="13" cy="13" r="12" fill="none" stroke="#fff" stroke-width="2"/><path d="M9 7l3 3-1.6 1.8c.8 1.7 2.1 3 3.8 3.8L16 14l3 3-2 2c-5 0-10-5-10-10z" fill="#fff"/></svg>
      0400 123 987
    </div>
  </div>
  <svg class="play" viewBox="0 0 68 68" aria-label="Play explainer video"><circle cx="34" cy="34" r="32" fill="rgba(0,0,0,.55)" stroke="#fff" stroke-width="2"/><path d="M27 21l20 13-20 13z" fill="#fff"/></svg>
  <h1 class="hero-title">BRIGHT PATH BUSINESS COACH</h1>
  <p class="hero-sub">Neque porro quisquam est qui dolorem ipsum quia dolor sit amet,</p>
  <div class="btn-outline-light">Free Download</div>
</section>

<section class="intro">
  <svg class="intro-icon" viewBox="0 0 116 116"><circle cx="58" cy="58" r="54" fill="#fff" stroke="#0a5bb0" stroke-width="4"/><circle cx="58" cy="54" r="14" fill="none" stroke="#0a5bb0" stroke-width="4"/><rect x="51" y="68" width="14" height="10" fill="#0a5bb0"/><g stroke="#0a5bb0" stroke-width="3"><path d="M58 28v-8M36 54h-8M88 54h-8M42 38l-6-6M74 38l6-6"/></g></svg>
  <div class="intro-text">
    <p>Bright Path Business Coach is here to help, support and turn your small business around. It may not be easy, it may not be pretty, it may not be conventional or what you want to hear but my only goal is to help you succeed in your small business in Australia.</p>
    <p>I offer a 12 week fully supported and personally applied program, each week you complete the activities and we meet over video call where your actions are accountable and measurable. Every business and small business owner are different, so not one solution fits all, and that's exactly why I can make it personal for those who want to change and need it to happen now.</p>
  </div>
</section>

<section class="snapshot">
  <div class="frame-line"></div>
  <div class="photo" role="img" aria-label="Photo of hands working on a laptop with charts"></div>
  <div class="snapshot-body">
    <h2>Australian Small Business Snapshot</h2>
    <div class="date">Nov 26, 2018</div>
    <p>It's an extremely sad sign of the times when you are confronted with a myriad of 'for lease' signs in shop windows along main shopping hubs. While most focus on cost, small businesses in Australia are small &ndash; accounting for 97 percent of all businesses &ndash; they're shutting their doors at alarmingly high numbers.</p>
    <ul class="checklist">
      <li>What is the Small Business Failure Rate?</li>
      <li>20% of small businesses fail in their first year</li>
      <li>30% of small businesses fail in their second year</li>
      <li>50% of small businesses fail after five years in business</li>
      <li>Finally, 70% of small business owners fail in their 10th year in business.</li>
    </ul>
  </div>
</section>

<section class="offers" role="img" aria-label="Faded background photo of a business meeting with charts">
  <svg class="slide-arrow prev" viewBox="0 0 26 40"><path d="M20 6L8 20l12 14" fill="none" stroke="#666" stroke-width="3"/></svg>
  <svg class="slide-arrow next" viewBox="0 0 26 40"><path d="M6 6l12 14L6 34" fill="none" stroke="#666" stroke-width="3"/></svg>
  <div class="card c1">
    <div class="price">Free</div>
    <h3>Giving Back</h3>
    <p>Bright Path Business Coach is offering a FREE 12-week coaching one-on-one support program every 3 months to struggling businesses in 2019 as our way of giving back and helping.</p>
    <span class="btn-small">Read more</span>
  </div>
  <div class="card c2">
    <div class="price">$200</div>
    <h3>Special Offer -<br>week for 12 weeks</h3>
    <p>Bright Path Business Coach is offering this incredible one on one support program to only 12 small business owners in the first quarter in 2019 at below cost, so if you need help now.</p>
    <span class="btn-small">Read more</span>
  </div>
  <div class="card c3">
    <div class="price">$400</div>
    <h3>Just A Bit -<br>week for 12 weeks</h3>
    <p>Very limited on application only, just 4 clients per quarter. Here we provide additional one on one support each week and dive deeper into every element of your business and fast.</p>
    <span class="btn-small">Read more</span>
  </div>
</section>

<section class="how">
  <div class="how-body">
    <h2>How it all works</h2>
    <p>With your permission I breakdown your business, Staff, Products / Services, Marketing and Sales. Under each of these four key components we go to 30 or more components including your staff training and experience, business financials, public exposure and engagement with target market, current marketing and processes required to make income.</p>
    <span class="btn-orange">Read more</span>
  </div>
  <div class="frame-line"></div>
  <div class="photo" role="img" aria-label="Photo of a hand pointing at financial charts on a screen"></div>
</section>

<section class="activities">
  <div class="wood" role="img" aria-label="Photo of people reviewing documents on a wooden desk"></div>
  <div class="activities-panel">
    <h2>Activates include</h2>
    <ul class="checklist">
      <li>Getting a measurable base line of the financials and existing marketing.</li>
      <li>Discussing the gaps (ups and downs) and looking forward to the future.</li>
      <li>Understanding your product or service and how it fits into the current marketplace.</li>
      <li>Looking into the staff for potential opportunities or training.</li>
      <li>Understanding market trends and conducting a SWOT analysis.</li>
      <li>Looking to establish a mastermind local group with a successful business.</li>
      <li>Partnership opportunities.</li>
      <li>Creating and applying marketing objectives.</li>
      <li>How to give more to grow.</li>
      <li>External learning materials applied as per needs, such as specific podcast episodes or suggested books that relate to a special need to be supported.</li>
    </ul>
  </div>
</section>

<section class="application">
  <h2>Application</h2>
  <p>Placements are strictly limited to 28 per quarter as they are all managed personally for the best possible outcomes. You must have internet access, put the time aside between 1-2 hours a week on video call and be open to change and motivated and accountable to succeed with every scheduled meeting.</p>
  <a>10 Things you can start today in your small business to get you going again!</a>
</section>

<section class="about">
  <div class="about-body">
    <h2>About Me</h2>
    <p>I am not superman, I just found myself absorbing information over the past 10 years through some mentors and personal development and see so many small business owners struggling and I got sick of telling myself how I would change things that I eventually approached some businesses for free and asked if they needed a hand and they were over the moon, very receptive and after a 1 hour talk the immediate action taken saw some massive returns exceeding even my estimates and now I just want to help more Small Business Owners through Bright Path Business Coach support.</p>
  </div>
  <div class="frame-line"></div>
  <div class="photo" role="img" aria-label="Portrait photo of the coach working at a laptop"></div>
</section>

<footer class="site-footer">
  <div class="footer-brand">
    <div class="brand">Bright Path Business Coach</div>
    <div class="socials" aria-label="Social links"><span></span><span></span><span></span><span></span><span></span></div>
  </div>
  <div class="footer-col col-contact">
    <h4>CONTACT US</h4>
    <div class="contact-item">
      <svg width="22" height="18" viewBox="0 0 22 18"><rect x="1" y="1" width="20" height="16" fill="none" stroke="#fff" stroke-width="2"/><path d="M1 1l10 8 10-8" fill="none" stroke="#fff" stroke-width="2"/></svg>
      <div><b>EMAIL ADDRESS</b><span>hello@brightpathcoach.com.au</span></div>
    </div>
    <div class="contact-item">
      <svg width="22" height="22" viewBox="0 0 26 26"><path d="M7 3l5 5-2.5 2.8c1.2 2.6 3.2 4.6 5.8 5.8L18 14l5 5-3 3C11 22 4 15 4 6z" fill="#fff"/></svg>
      <div><b>PHONE NUMBER</b><span>(02) 5550 1928</span></div>
    </div>
  </div>
  <div class="footer-col col-about">
    <h4>ABOUT</h4>
    <ul><li>Home</li><li>About Us</li><li>Services</li><li>Products</li></ul>
  </div>
  <div class="footer-col col-res">
    <h4>RESOURCES</h4>
    <ul><li>News</li><li>Support</li><li>Faq</li><li>Contact</li></ul>
  </div>
</footer>
<div class="copyright">&copy; 2018 Company Name. All right reserved</div>

</body>
</html>
```